Custom Wordpress Theme - Original and Professional

We are a boutique IT consulting firm that provide small and medium business in Australia three different levels of IT service.
We are looking for a developer who will create a customised, original and professional wordpress theme. We are looking for the developer to create a professional, clean, clear and simple theme with a stylish layout, images and icons.
Our three services are: IT support | IT Services | IT Solutions and we would like to clearly differentiate the difference in each level of service in as few words as possible.
IT Support is the ad hock “call us, when you need us” service, that smaller business or those with minimal issues use.
IT service is the unlimited service, that business with existing (and well maintained) IT systems choose and is both flexible and scalable including no contracts or paperwork required.
IT solutions are the unlimited service that businesses that need new or updated infrastructure choose and it includes all the hardware, software and services with no contracts or any ongoing commitment.
The main page on the web site will attract the visitor to choose the right “service level” for their business and then we will have a dedicated page for each service and another page for a comparison (table) to compare all three services.
Lastly we will need a contact us page that has both office locations (Sydney and Melbourne), contact phone numbers and an email form.
Items we are focused on for this project are: 1. Images, 2.Icons 3. Layout.
In summary we are looking for a custom WordPress theme into a 6 page (Home, IT Support, IT Services, IT Solutions, Compare Service levels and Contact us) website. The design must include relevant images and icons and be clear, simple, professional and sleek.

Thank you for your time and creativity and I look forward to working with you!

Target Market(s)

Small and Medium businesses in Australia

Industry/Entity Type

Boutique

Requirements
Must have
• - 6 Pages layout: Home, IT support, IT services, IT Solutions, Compare service levels and Contact us
- Images, Layout and Icons.
- Clean, Clear, Simple, Elegant, Stylish.
Nice to have
• - Some text (if possible but not required).
Should not have
• - Complexity.
- Confusing layout.
- Generic non matching images and icons.

```html
<!DOCTYPE html>
<html lang="en">
<head>
<meta charset="utf-8">
<title>Coreline IT – IT Support</title>
<link href="https://fonts.googleapis.com/css2?family=Michroma&family=Syncopate:wght@400;700&family=Aldrich&family=Oswald:wght@300&family=Russo+One&display=swap" rel="stylesheet">
<style>
:root{
  --blue:#0f5eae;
  --blue-bright:#1476c8;
  --blue-deep:#0b4d92;
  --ink:#2e2e2e;
  --body-text:#3a3a3a;
  --active:#333333;
  --footer-bg:#353433;
  --footer-text:#c9c9c9;
  --footer-head:#e6e6e6;
  --quote-text:#a9a9a9;
  --social:#8c8c8c;
  --hero-warm:#b9aaa0;
  --hero-light:#cfc4bc;
  --hero-cool:#9c9490;
  --white:#ffffff;
}
*{margin:0;padding:0;box-sizing:border-box}
html,body{width:1128px;height:1200px;overflow:hidden;background:var(--white)}
body{font-family:Arial,Helvetica,sans-serif;color:var(--body-text)}
.page{position:relative;width:1128px;height:1200px}

/* header */
.site-header{position:relative;height:90px}
.brand{position:absolute;left:40px;top:22px;display:flex;align-items:center;gap:14px;
  font-family:"Michroma",sans-serif;font-size:38px;color:var(--blue);letter-spacing:3px;line-height:1}
.brand-dot{width:22px;height:22px;background:var(--blue)}
.enquiry{position:absolute;right:20px;top:14px;text-align:right}
.enquiry-label{font-family:"Aldrich",sans-serif;font-size:16px;color:var(--blue);letter-spacing:.5px}
.enquiry-phone{display:flex;align-items:center;justify-content:flex-end;gap:8px;margin-top:4px;
  font-family:"Oswald",sans-serif;font-weight:300;font-size:30px;color:var(--ink);line-height:1}

/* nav */
.main-nav{height:52px;background:linear-gradient(var(--blue-bright),var(--blue));border-bottom:6px solid var(--blue-deep);
  display:flex;padding-left:17px}
.main-nav a{position:relative;display:flex;align-items:center;padding:0 16px;height:46px;
  font-family:"Michroma",sans-serif;font-size:15px;letter-spacing:1px;color:var(--white);text-decoration:none;white-space:nowrap}
.main-nav a.is-active{background:var(--active)}
.main-nav a.is-active::before{content:"";position:absolute;left:50%;top:0;margin-left:-9px;
  border:9px solid transparent;border-top-color:var(--white);border-bottom:0}

/* hero */
.hero{height:278px;margin-top:5px;
  background:linear-gradient(90deg,var(--hero-warm) 0%,var(--hero-light) 55%,var(--hero-cool) 100%)}

/* content */
.content{position:relative;height:510px}
.service-icon{position:absolute;left:45px;top:35px}
.service-text{position:absolute;left:281px;top:50px;width:812px}
.service-title{font-family:"Syncopate","Russo One",sans-serif;font-weight:700;font-size:38px;color:var(--ink);letter-spacing:0;line-height:1;margin-bottom:18px}
.service-text p{font-size:16px;line-height:19.4px;margin-bottom:19px}

/* footer */
.site-footer{position:absolute;left:0;top:935px;width:1128px;height:265px;background:var(--footer-bg)}
.footer-head{font-family:"Russo One",sans-serif;font-size:19px;color:var(--footer-head);letter-spacing:.5px;margin-bottom:14px;font-weight:400}
.footer-nav{position:absolute;left:36px;top:38px}
.footer-nav a{display:block;font-size:14px;line-height:18.4px;color:var(--footer-text);text-decoration:none}
.testimonial{position:absolute;left:373px;top:38px;width:380px}
.testimonial-body{display:flex;gap:14px}
.testimonial-body p{font-size:13.5px;line-height:16.6px;color:var(--quote-text);width:300px}
.testimonial-author{font-size:16px;color:var(--white);margin-top:8px}
.footer-contact{position:absolute;left:871px;top:38px;width:230px}
.social{display:flex;gap:9px;margin-bottom:12px}
.social span{width:32px;height:32px;border-radius:50%;background:var(--social)}
.newsletter-note{font-size:12px;line-height:15px;color:var(--white);margin-bottom:10px;width:210px}
.newsletter-input{width:215px;height:31px;border-radius:16px;background:#eaeaea;
  font-size:12px;color:#333;line-height:31px;padding-left:18px;margin-left:-6px}
.newsletter-submit{margin-top:15px;font-size:12px;font-weight:bold;color:var(--white);display:flex;align-items:center;gap:8px}
</style>
</head>
<body>
<div class="page">
  <header class="site-header">
    <div class="brand"><span class="brand-dot"></span>Coreline IT</div>
    <div class="enquiry">
      <div class="enquiry-label">FOR SERVICES &amp; INQUIRIES</div>
      <div class="enquiry-phone">
        <svg width="30" height="30" viewBox="0 0 30 30" aria-hidden="true">
          <circle cx="15" cy="15" r="13.5" fill="none" stroke="#2e2e2e" stroke-width="2"/>
          <path d="M10 8c1-1 2-1 3 0l1.5 2.5c.5 1 0 1.8-.8 2.3-.5.3-.5 1 0 1.8l1.5 1.8c.6.7 1.3.8 1.8.2.7-.8 1.6-1 2.4-.4l2.2 1.7c.9.8.8 1.8-.2 2.8-2 2-5 1-8-2s-5-7.5-3.4-10.7z" fill="#2e2e2e"/>
        </svg>
        0-98-7654321
      </div>
    </div>
  </header>

  <nav class="main-nav">
    <a href="#">HOME</a>
    <a href="#" class="is-active">IT SUPPORT</a>
    <a href="#">IT SERVICES</a>
    <a href="#">IT SOLUTIONS</a>
    <a href="#">COMPARE IT SERVICE</a>
    <a href="#">CONTACT US</a>
  </nav>

  <div class="hero" role="img" aria-label="Banner photograph of a human eye overlaid with digital data and binary code"></div>

  <main class="content">
    <svg class="service-icon" width="184" height="184" viewBox="0 0 184 184" role="img" aria-label="Support agent wearing a headset icon">
      <circle cx="92" cy="92" r="92" fill="#0f5eae"/>
    </svg>
    <section class="service-text">
      <h1 class="service-title">IT SUPPORT</h1>
      <p>Lorem ipsum dolor sit amet, consectetur adipisicing elit, sed do eiusmod tempor incididunt ut labore et dolore magna aliqua. Ut enim ad minim veniam, quis nostrud exercitation ullamco laboris nisi ut aliquip ex ea commodo consequat. Duis aute irure dolor in reprehenderit in voluptate velit esse cillum dolore eu fugiat nulla pariatur. Excepteur sint occaecat cupidatat non proident, sunt in culpa qui officia deserunt mollit anim id est laborum.</p>
      <p>Sed ut perspiciatis, unde omnis iste natus error sit voluptatem accusantium doloremque laudantium, totam rem aperiam eaque ipsa, quae ab illo inventore veritatis et quasi architecto beatae vitae dicta sunt, explicabo. Nemo enim ipsam voluptatem, quia voluptas sit, aspernatur aut odit aut fugit, sed quia consequuntur magni dolores eos, qui ratione voluptatem sequi nesciunt, neque porro quisquam est, qui dolorem ipsum, quia dolor sit amet, consectetur, adipisci[ng] velit, sed quia non numquam [do] eius modi tempora inci[di]dunt, ut labore et dolore magnam aliquam quaerat voluptatem.</p>
      <p>&nbsp;At vero eos et accusamus et iusto odio dignissimos ducimus, qui blanditiis praesentium voluptatum deleniti atque corrupti, quos dolores et quas molestias excepturi sint, obcaecati cupiditate non provident, similique sunt in culpa, qui officia deserunt mollitia animi, id est laborum et dolorum fuga. Et harum quidem rerum facilis est et expedita distinctio. Nam libero tempore, cum soluta nobis est eligendi optio, cumque nihil impedit, quo minus id, quod maxime placeat, facere possimus, omnis voluptas assumenda est, omnis dolor repellendus.</p>
    </section>
  </main>

  <footer class="site-footer">
    <div class="footer-nav">
      <h2 class="footer-head">NAVIGATION</h2>
      <a href="#">Home</a>
      <a href="#">IT support</a>
      <a href="#">IT Services</a>
      <a href="#">IT Solutions</a>
      <a href="#">Compare IT Service</a>
      <a href="#">Contact Us</a>
    </div>
    <div class="testimonial">
      <h2 class="footer-head">TESTIMONIAL</h2>
      <div class="testimonial-body">
        <svg width="52" height="50" viewBox="0 0 52 50" aria-hidden="true">
          <ellipse cx="20" cy="17" rx="18" ry="14" fill="none" stroke="#9a9a9a" stroke-width="3"/>
          <path d="M8 28l-4 9 10-6z" fill="#9a9a9a"/>
          <ellipse cx="34" cy="32" rx="16" ry="13" fill="#9a9a9a"/>
          <path d="M44 42l4 8-10-5z" fill="#9a9a9a"/>
        </svg>
        <p>At vero eos et accusamus et iusto odio dignissimos ducimus, qui blanditiis praesentium voluptatum deleniti atque corrupti, quos dolores et quas molestias excepturi sint.”</p>
      </div>
      <div class="testimonial-author">- Daniel Harper</div>
    </div>
    <div class="footer-contact">
      <h2 class="footer-head">CONTACT US</h2>
      <div class="social"><span></span><span></span><span></span><span></span><span></span></div>
      <p class="newsletter-note">subscribe to our monthly newsletter and get the best deals and discounts</p>
      <div class="newsletter-input">enter email address</div>
      <div class="newsletter-submit">
        <svg width="12" height="10" viewBox="0 0 12 10" aria-hidden="true"><path d="M0 0l12 5-12 5 3-5z" fill="#fff"/></svg>
        subscribe now
      </div>
    </div>
  </footer>
</div>
</body>
</html>
```